Etikett für Rotweinflasche
Liebe farbkosmos Atelier, wir werden uns bei der endgültigen Etikettengestaltung (finale Größe + Rückseite) noch an Euch melden. Bitte sendet uns euren Kontakt an helga.brandt@morvelli.wine
Zielgruppe
Morvelli Italia ist ein exklusives Boutique-Weingut in Sizilien, das hochqualitative Spitzenweine in kleinen Mengen mit modernster Technologie und stets nachhaltig erzeugt. Wir hinterfragen sowohl in der Agronomie im Weingarten als auch in der Önologie im Weinkeller alle herrschenden Traditionen und trachten danach, stets das beste Endprodukt zu kreieren. Der vulkanische, kalkreiche Boden Siziliens sowie trockene, sonnenreiche und niederschlagsarme Vegetationsperioden sind unsere optimale Basis.
Zielgruppe: Internationale Genussmenschen jeglichen Alters, die sich bewusst auch höherpreisige Weine (um die €30+) gönnen , vor allem kunstaffine young professionals mit Qualitäts-& Nachhaltigkeitsanspruch
Aufgabenstellung
Das Etikett ist für Rotwein-Flaschen (Cabernet Sauvignon / Nero D'Avola / Frappato / Syrah / Cerasuolo / Petit Verdot / sowie einen Bourdeaux-Cuveè aus Cabernet Sauvignon und Petit Verdot) .
Die Flasche ist reinschwarz, sehr hochwertig und schwer.
Flaschenform: Bordeauxflasche siehe technisches Datenblatt
Sleeve über dem Korken: schwarz mit weißer Schrift wie bisher
Zu gestalten ist das Etikett der Vorderseite. Zumindest die jeweilige Rotwein-Sorte ist auch textlich darzustellen (zwecks Scannen mit Trubel-App)
Der Kreativität kann freien Lauf gelassen werden! Unterscheidbarkeit vom Markt ist explizit gewollt.
Unsere aktuellen Etiketten und Markenauftritt siehe: https://morvelli.wine/shop/

```html
<!DOCTYPE html>
<html lang="de">
<head>
<meta charset="utf-8">
<title>Etikett Cabernet Sauvignon – Morvelli Italia</title>
<link rel="stylesheet" href="https://fonts.googleapis.com/css2?family=Cormorant+Garamond:wght@500&display=swap">
<style>
  :root {
    --page-bg: #ffffff;
    --label-bg: #f7dccf;
    --ink: #4b4d8a;
    --art-navy: #34419a;
    --art-red: #e2414d;
    --art-magenta: #d0305e;
    --art-orange: #f2a257;
    --art-gold: #f1c25e;
    --art-blush: #f6e2da;
  }
  html, body {
    margin: 0;
    padding: 0;
    width: 740px;
    height: 1200px;
    overflow: hidden;
    background: var(--page-bg);
  }
  .canvas {
    position: relative;
    width: 740px;
    height: 1200px;
    display: flex;
    align-items: center;
    justify-content: center;
  }
  .wine-label {
    position: relative;
    width: 740px;
    height: 1062px;
    background: var(--label-bg);
    overflow: hidden;
  }
  .label-art {
    position: absolute;
    left: 0;
    top: 0;
    width: 740px;
    height: 1062px;
    display: block;
  }
  .varietal {
    position: absolute;
    left: 0;
    right: 0;
    top: 948px;
    margin: 0;
    text-align: center;
    font-family: "Cormorant Garamond", "Times New Roman", serif;
    font-weight: 500;
    font-size: 31px;
    letter-spacing: 0.24em;
    color: var(--ink);
    text-transform: uppercase;
    padding-right: 14px;
  }
</style>
</head>
<body>
  <main class="canvas">
    <section class="wine-label">
      <svg class="label-art" viewBox="0 0 740 1062" role="img" aria-label="Abstrakte Komposition aus sich überlagernden, körnigen Dreiecken in Marineblau, Rot, Magenta, Orange und Gold auf zartem Rosé">
        <defs>
          <linearGradient id="art-wash" x1="0" y1="0" x2="1" y2="1">
            <stop offset="0" stop-color="var(--art-navy)"/>
            <stop offset="0.35" stop-color="var(--art-red)"/>
            <stop offset="0.55" stop-color="var(--art-magenta)" stop-opacity="0.85"/>
            <stop offset="0.75" stop-color="var(--art-orange)"/>
            <stop offset="1" stop-color="var(--art-blush)"/>
          </linearGradient>
          <linearGradient id="art-fade" x1="0" y1="0" x2="1" y2="0">
            <stop offset="0" stop-color="var(--label-bg)" stop-opacity="0"/>
            <stop offset="0.7" stop-color="var(--label-bg)" stop-opacity="0.35"/>
            <stop offset="1" stop-color="var(--label-bg)" stop-opacity="0.9"/>
          </linearGradient>
        </defs>
        <rect x="0" y="0" width="740" height="860" fill="url(#art-wash)"/>
        <rect x="0" y="0" width="740" height="860" fill="url(#art-fade)"/>
        <rect x="120" y="860" width="250" height="202" fill="var(--art-orange)" opacity="0.55"/>
      </svg>
      <h1 class="varietal">Cabernet Sauvignon</h1>
    </section>
  </main>
</body>
</html>
```